ambitious event and festival agency from austria needs fresh business card design

A new design is due for the new headquarters and the new challenges. We organize events for different target groups from 16 to 60 years. The design should therefore be straightforward and not confused, so we are open to new colors and the logo may also be changed. In general, however, the most interesting suggestions are the most interesting ones. after this order we are looking for more graphics for halvenrush facebook instagramm homepage etc A new design is due for the new headquarters and the new challenges. We organize events for different target groups from 16 to 60 years. The design should therefore be straightforward and not confused, so we are open to new colors and the logo may also be changed. In general, however, the most interesting suggestions are the most interesting ones. after this order we are looking for more graphics for halvenrush facebook instagramm homepage etc A new design is due for the new headquarters and the new challenges. We organize events for different target groups from 16 to 60 years. The design should therefore be straightforward and not confused, so we are open to new colors and the logo may also be changed. In general, however, the most interesting suggestions are the most interesting ones. after this order we are looking for more graphics for halvenrush facebook instagramm homepage etc
Updates

Reason: I am sorry for this decision but i need some more time. No new designs please, there are so many good ones and I will have made a decision in the next 3 days.

Target Market(s)

Industry/Entity Type

Business

Font styles to use
Serif
Sans Serif

Colors

Designer to choose colors to be used in the design.

Requirements
Must have
Nice to have
Should not have

```html
<!DOCTYPE html>
<html lang="en">
<head>
<meta charset="utf-8">
<title>halvenrush business card</title>
<link rel="stylesheet" href="https://fonts.googleapis.com/css2?family=Lato:wght@400;700&display=swap">
<style>
  :root {
    --backdrop: #3b3b3d;
    --brand-red: #c02d3c;
    --brand-red-light: #c9434f;
    --card-dark: #1b2127;
    --card-dark-light: #232a31;
    --text-grey: #8d9296;
    --text-light: #f2f2f2;
  }
  html, body {
    margin: 0;
    width: 1200px;
    height: 900px;
    overflow: hidden;
    background: var(--backdrop);
    font-family: "Lato", sans-serif;
  }
  .card {
    position: absolute;
    left: 300px;
    width: 600px;
    height: 340px;
    border-radius: 18px;
    box-sizing: border-box;
    overflow: hidden;
  }
  .card-front {
    top: 90px;
    background: linear-gradient(100deg, var(--brand-red-light) 0%, var(--brand-red) 60%);
  }
  .card-back {
    top: 470px;
    background: linear-gradient(100deg, var(--card-dark-light) 0%, var(--card-dark) 60%);
  }
  .wordmark {
    position: absolute;
    font-weight: 400;
    letter-spacing: 0.5px;
    line-height: 1;
    white-space: nowrap;
  }
  .card-front .wordmark {
    right: 56px;
    top: 140px;
    font-size: 56px;
    color: var(--text-light);
  }
  .card-back .wordmark {
    left: 44px;
    top: 190px;
    font-size: 44px;
    color: var(--brand-red);
  }
  .divider {
    position: absolute;
    left: 322px;
    top: 56px;
    width: 2px;
    height: 230px;
    background: var(--brand-red);
  }
  .contact {
    position: absolute;
    left: 346px;
    top: 60px;
    color: var(--text-grey);
  }
  .person-name {
    font-size: 24px;
    margin: 0;
  }
  .job-title {
    font-size: 14px;
    color: var(--brand-red);
    margin: 2px 0 18px 14px;
  }
  .contact-list {
    list-style: none;
    margin: 0;
    padding: 0 0 0 24px;
    font-size: 15px;
  }
  .contact-list li {
    display: flex;
    align-items: center;
    gap: 8px;
    margin-bottom: 12px;
    white-space: nowrap;
  }
  .contact-list svg {
    width: 16px;
    height: 16px;
    flex: none;
  }
  .social-square {
    width: 14px;
    height: 14px;
    background: var(--brand-red);
    border-radius: 2px;
    flex: none;
  }
</style>
</head>
<body>
  <section class="card card-front">
    <span class="wordmark">halvenrush</span>
  </section>

  <section class="card card-back">
    <span class="wordmark">halvenrush</span>
    <div class="divider"></div>
    <div class="contact">
      <p class="person-name">Your Name</p>
      <p class="job-title">Job title</p>
      <ul class="contact-list">
        <li>
          <svg viewBox="0 0 16 16" aria-hidden="true"><path fill="#c02d3c" d="M2 5c0-2 3-3 6-3s6 1 6 3v1h-3V5H5v1H2zM3 7h10l1 6H2zM8 8.5a2 2 0 1 0 0 4 2 2 0 0 0 0-4z"/></svg>
          000 000 0000
        </li>
        <li>
          <svg viewBox="0 0 16 16" aria-hidden="true"><rect x="1" y="3" width="14" height="10" fill="#c02d3c"/><path d="M1 3l7 6 7-6" stroke="#1b2127" stroke-width="1.4" fill="none"/></svg>
          hello@halvenrush.com
        </li>
        <li>
          <svg viewBox="0 0 16 16" aria-hidden="true" fill="none" stroke="#8d9296" stroke-width="1.2"><circle cx="8" cy="8" r="6.5"/><ellipse cx="8" cy="8" rx="3" ry="6.5"/><path d="M1.5 8h13M2.5 5h11M2.5 11h11"/></svg>
          halvenrush-events.com
        </li>
        <li>
          <span class="social-square"></span>
          /halvenrush
        </li>
      </ul>
    </div>
  </section>
</body>
</html>
```